Velk Partners Building Business Cards

We need a business card that reflects our business as "Solar Experts" in San Diego. Browse our website www.velkpartners.example our License needs to be displayed as "CSLB# 3867140" our phone number is (619) 555-0187

Save thousands on your electric bills and increase the value of your home while helping to protect the environment. Our solar installation experts will help you design the system that's right for you, using only the highest quality equipment that will look great and give you ideal performance. Our goal is to make you energy independent, and get your electric bill to 0.

Paul Osterby
(619) 555-0187
paul@velkpartners.example

Target Market(s)

Home owners in san diego looking for solar

Industry/Entity Type

Solar Energy

Contact Information for Business Card

Paul Osterby
(619) 555-0187
paul@velkpartners.example

Font styles to use
Other font styles liked:
• Use our logo font

Requirements
Must have
• License needs to be displayed as "CSLB# 3867140" our phone number is (619) 555-0187
Nice to have
• Real images of rooftop home solar in san diego
Should not have
• our business address

```html
<!DOCTYPE html>
<html lang="en">
<head>
<meta charset="utf-8">
<title>Velk Partners Building — Business Card</title>
<link rel="stylesheet" href="https://fonts.googleapis.com/css2?family=Open+Sans:wght@400;700;800&display=swap">
<style>
  :root {
    --navy: #1f3d7a;
    --gold: #f5a800;
    --white: #ffffff;
    --ink: #1b1b1b;
    --stage: #ecebe8;
  }
  * { box-sizing: border-box; margin: 0; padding: 0; }
  html, body {
    width: 1200px; height: 900px; overflow: hidden;
    background: var(--stage);
    font-family: "Open Sans", Arial, sans-serif;
  }
  .canvas { position: relative; width: 1200px; height: 900px; }

  .card {
    position: absolute;
    width: 640px; height: 366px;
    overflow: hidden;
    box-shadow: 0 6px 18px rgba(0,0,0,.18);
  }

  /* Back side */
  .card--back { left: 480px; top: 60px; background: var(--navy); }
  .card--back .brand {
    position: absolute; left: 0; right: 0; top: 50%;
    transform: translateY(-50%);
    display: flex; align-items: center; justify-content: center; gap: 14px;
    color: var(--white);
  }

  .brand-dot {
    width: 26px; height: 26px; border-radius: 50%;
    background: var(--gold); flex: none;
  }
  .brand-name {
    font-weight: 800; font-size: 40px; letter-spacing: -0.5px;
    line-height: 1;
  }

  /* Front side */
  .card--front { left: 100px; top: 480px; background: var(--white); }
  .card-decor { position: absolute; inset: 0; width: 640px; height: 366px; }

  .holder-name {
    position: absolute; left: 66px; top: 30px;
    font-weight: 700; font-size: 19px;
  }
  .holder-name .first { color: var(--navy); }
  .holder-name .last { color: var(--gold); }

  .card--front .brand {
    position: absolute; left: 300px; top: 150px;
    display: flex; align-items: center; gap: 10px;
    color: var(--navy);
  }
  .card--front .brand-name { font-size: 31px; }
  .card--front .brand-dot { width: 20px; height: 20px; }

  .contact {
    position: absolute; left: 36px; top: 172px;
    font-size: 15px; color: var(--ink); line-height: 1.55;
    list-style: none;
  }
  .contact .license-label { color: var(--navy); font-weight: 700; }
  .contact li { display: flex; align-items: center; gap: 9px; }
  .contact .icon { width: 14px; height: 14px; flex: none; }
  .contact .license { margin-left: 0; }
</style>
</head>
<body>
<main class="canvas">

  <section class="card card--back" aria-label="Business card back">
    <div class="brand">
      <span class="brand-dot"></span>
      <span class="brand-name">Velk Partners Building</span>
    </div>
  </section>

  <section class="card card--front" aria-label="Business card front">
    <svg class="card-decor" viewBox="0 0 640 366" aria-hidden="true">
      <polygon points="0,0 58,0 0,38" fill="var(--navy)"/>
      <polygon points="44,14 74,0 62,36 30,36" fill="var(--gold)"/>
      <polygon points="0,248 270,300 255,312 0,276" fill="var(--navy)"/>
      <polygon points="268,306 640,336 640,366 232,366" fill="var(--gold)"/>
    </svg>

    <p class="holder-name"><span class="first">Paul</span> <span class="last">Osterby</span></p>

    <div class="brand">
      <span class="brand-name">Velk Partners Building</span>
      <span class="brand-dot"></span>
    </div>

    <ul class="contact">
      <li class="license"><span><span class="license-label">License:</span> CSLB# 3867140</span></li>
      <li>
        <svg class="icon" viewBox="0 0 24 24" aria-hidden="true"><path fill="var(--gold)" d="M6.6 10.8a15 15 0 0 0 6.6 6.6l2.2-2.2a1 1 0 0 1 1-.25 11.4 11.4 0 0 0 3.6.6 1 1 0 0 1 1 1V20a1 1 0 0 1-1 1A17 17 0 0 1 3 4a1 1 0 0 1 1-1h3.5a1 1 0 0 1 1 1c0 1.25.2 2.45.6 3.6a1 1 0 0 1-.25 1z"/></svg>
        <span>(619) 555-0187</span>
      </li>
      <li>
        <svg class="icon" viewBox="0 0 24 24" aria-hidden="true"><rect x="2" y="5" width="20" height="14" rx="1.5" fill="var(--gold)"/><path d="M3 6l9 7 9-7" fill="none" stroke="#fff" stroke-width="1.6"/></svg>
        <span>paul@velkpartners.example</span>
      </li>
    </ul>
  </section>

</main>
</body>
</html>
```